Project Overview:
We are looking to create a website for a monthly subscription IPTV service in WordPress. The website should provide a seamless user experience for customers to sign up for the service and manage their account information. We need the following pages: Home Page, Product Page, Sign-Up Page, and Account Information Page.

Home Page:
The Home Page design should be simple and clean, with a dark theme and minimalistic design elements. We would like to include graphics of popular movie shows displayed on multiple devices. The page should highlight the key benefits and features of our service and provide a clear call-to-action for visitors to sign up.

Product Page:
The Product Page should provide detailed information about our subscription tiers and pricing plans. It should highlight the key features of each plan and provide a clear comparison between them. The page should also include a call-to-action button for visitors to sign up.

Sign-Up Page:
The Sign-Up Page is the conversion page where members will sign up for the service. It should collect the following information: Name, Phone Number, Email, Password, and Payment Information. The design should be simple, intuitive, and easy to use. It should highlight the benefits of our service and provide a clear call-to-action for visitors to sign up.

Account Information Page:
The Account Information Page should allow members to view and manage their account details. It should include the following information: Profile Image, Contact Details, Password Management, Payment Information Management, and Membership Expiration Date. The design should be user-friendly, intuitive, and easy to navigate.

Goals: The primary goal of the website is to provide an easy-to-use portal for customers to sign up for the service and manage their account information. The website should be user-friendly and visually appealing to attract potential customers.

Scope: The scope of the project includes designing a home page, a sign-up page, an account information page, and a payment information page. The website should be designed to be responsive and accessible on desktop and mobile devices.

Design Preferences: The design should be clean, modern, and visually appealing. The use of a color palette that is consistent with the brand identity is recommended. The website should be easy to navigate and provide a clear call-to-action for users to sign up for the service.

FYI: The subscription service I am designing a website for is related to an IPTV service. IPTV stands for Internet Protocol Television, which is a digital television broadcasting protocol that uses the internet to deliver TV programs and videos to viewers. The website will allow customers to sign up for the IPTV service and access their account information such as user name and password, membership tier, name, and payment details. Please let me know if you have any further questions, and I would be happy to provide more details. Thank you!

Dear Designers,

Thank you for your participation in our project. After reviewing the designs received so far, we have decided to update the brief to better reflect our needs and preferences. We apologize for any confusion this may cause, but we believe that these changes will result in better design submissions and a more successful project overall.

The updated brief is as follows:

We are looking to create a website for WordPress.

Also, here is the updated Brief.

Project Title: WordPress Website Design for Monthly Subscription IPTV Service

Project Overview:
We are looking to create a website for a monthly subscription IPTV service. The website should provide a seamless user experience for customers to sign up for the service and manage their account information. We need the following pages: Home Page, Product Page, Sign-Up Page, and Account Information Page.

Home Page:

Product Page:

Sign-Up Page:

Account Information Page:

Design Preferences:
We prefer a dark theme with minimalistic design elements and hits of our logo colors. The website should be easy to use and navigate, with clear calls-to-action and simple, intuitive forms. The design should be optimized for mobile devices and load quickly.

We hope that these updates provide you with a clearer understanding of our requirements and preferences. Please let us know if you have any questions or concerns. We look forward to seeing your revised designs.

Thank you again for your participation.
We will guarantee this project as soon as we see something we like that meets the updated requirements.

The website's target audience is individuals who are interested in subscribing to the monthly service.

4 page

• One item for sale and a client profile section.

```html
<!DOCTYPE html>
<html lang="en">
<head>
<meta charset="UTF-8">
<title>Veltro — Streaming TV Subscription</title>
<link href="https://fonts.googleapis.com/css2?family=Roboto:wght@400;500;700;900&display=swap" rel="stylesheet">
<style>
:root{
  --red:#f50000;
  --red-deep:#c80000;
  --black:#050505;
  --ink:#111111;
  --text:#555555;
  --muted:#777777;
  --light:#f7f7f9;
  --grey:#ececec;
  --white:#ffffff;
}
*{margin:0;padding:0;box-sizing:border-box}
html,body{width:1200px;height:4118px;overflow:hidden}
body{position:relative;background:var(--white);font-family:'Roboto',sans-serif;color:var(--ink)}
.abs{position:absolute}
.btn{position:absolute;display:flex;align-items:center;justify-content:center;background:var(--red);color:var(--white);font-weight:700;font-size:16px;border-radius:5px;text-transform:uppercase;letter-spacing:.2px}
.brand{display:flex;align-items:center;gap:10px;font-weight:900;font-size:40px;letter-spacing:1px;color:var(--red)}
.brand .mark{width:22px;height:22px;background:var(--red)}
.brand.light{color:var(--white)}
.brand.light .mark{background:var(--red)}

/* header */
.top-line{left:0;top:0;width:1200px;height:4px;background:var(--red)}
.main-nav{top:94px;left:0;width:1200px;height:20px}
.main-nav a{position:absolute;font-size:16px;font-weight:700;color:var(--ink);text-decoration:none}

/* hero */
.hero-text{right:113px;top:270px;text-align:right;color:var(--white)}
.hero-text h1{font-size:66px;line-height:80px;font-weight:900;text-transform:uppercase}
.hero-text p{margin-top:28px;width:460px;margin-left:auto;font-size:18px;line-height:30px}

/* about */
.section-title{font-size:35px;font-weight:700;text-transform:uppercase;color:var(--ink)}
.about-copy{left:113px;top:985px;width:445px;font-size:14.5px;line-height:27.5px;color:var(--text)}
.about-photo{left:614px;top:884px;width:481px;height:466px;border:0 solid var(--white);background:linear-gradient(135deg,#b9c4cf 0%,#6c7a88 40%,#2c3440 60%,#c04a4a 100%);box-shadow:4px 4px 0 4px var(--white)}
.about-accent{left:920px;top:1214px;width:255px;height:221px;background:var(--red);border-radius:0 60px 0 70px}

/* services */
.services{left:0;top:1435px;width:1200px;height:866px;background:var(--light)}
.center{text-align:center;width:1200px;left:0}
.lead{font-size:15.5px;line-height:26px;color:var(--text)}
.card{position:absolute;top:1673px;width:315px;height:451px;background:var(--white);box-shadow:0 2px 10px rgba(0,0,0,.12);border-radius:3px;text-align:center}
.card .pic{margin:6px;height:224px}
.card h3{margin-top:30px;font-size:19px;font-weight:700}
.card p{margin:16px auto 0;width:276px;font-size:13.5px;line-height:22.5px;color:var(--text)}
.card a{display:inline-block;margin-top:10px;font-size:16px;font-weight:700;color:var(--red);text-decoration:underline}

/* signup */
.signup-text{color:var(--white)}
.field{position:absolute;top:2589px;width:203px;height:76px;border:2px solid rgba(255,255,255,.9);border-radius:5px;display:flex;align-items:center;padding-left:36px;color:var(--white);font-size:15px}
.field svg{position:absolute;right:16px}

/* faq */
.faq-photo{left:110px;top:3059px;width:432px;height:538px;background:linear-gradient(160deg,#dcdcdc 0%,#c9c2b8 45%,#5d738e 75%,#3b4a5c 100%)}
.faq-item{position:absolute;left:582px;width:509px;height:46px;border-radius:23px;display:flex;align-items:center;padding-left:62px;font-size:13px;font-weight:700;color:var(--ink);text-transform:uppercase}
.faq-item .sign{position:absolute;left:18px;top:14px;width:18px;height:18px}
.faq-item.open{background:var(--white);box-shadow:0 3px 12px rgba(0,0,0,.12)}
.faq-item.closed{background:var(--grey)}
.faq-answer{left:657px;top:3287px;width:420px;font-size:12px;line-height:22.5px;color:var(--muted)}
.faq-answer::before{content:"";position:absolute;left:-13px;top:4px;width:2px;height:48px;background:var(--red)}

/* footer */
.footer-nav a{position:absolute;top:3945px;font-size:16px;font-weight:700;color:var(--white);text-decoration:none}
.social{position:absolute;top:3997px;width:28px;height:28px;border-radius:50%;background:var(--white)}
.copyright{top:4055px;font-size:11.5px;color:var(--white)}
</style>
</head>
<body>

<!-- Header -->
<div class="abs top-line"></div>
<div class="abs brand" style="left:110px;top:54px"><span class="mark"></span>VELTRO</div>
<div class="btn" style="left:957px;top:27px;width:131px;height:50px">Sign Up</div>
<nav class="abs main-nav">
  <a style="left:462px">HOME</a>
  <a style="left:574px">ABOUT US</a>
  <a style="left:719px">OUR PLANS</a>
  <a style="left:876px">FAQ’S</a>
  <a style="left:986px">CONTACT US</a>
</nav>

<!-- Hero -->
<svg class="abs" style="left:0;top:150px" width="1200" height="605" viewBox="0 0 1200 605" role="img" aria-label="Wall of glowing TV screens showing news and channels">
  <defs>
    <linearGradient id="heroFill" x1="0" y1="0" x2="1" y2="0">
      <stop offset="0" stop-color="#1c4ea8"/>
      <stop offset=".3" stop-color="#123a80"/>
      <stop offset=".5" stop-color="#0b1a3a"/>
      <stop offset=".62" stop-color="#000000"/>
      <stop offset="1" stop-color="#000000"/>
    </linearGradient>
  </defs>
  <path d="M60 42 L1130 2 Q1200 0 1200 70 L1200 530 Q1200 602 1140 600 L70 568 Q0 566 0 500 L0 110 Q0 44 60 42 Z" fill="url(#heroFill)"/>
</svg>
<div class="abs hero-text">
  <h1>Welcome to<br>Veltro</h1>
  <p>"Sed ut perspiciatis unde omnis iste natus error sit voluptatem accusantium doloremque laudantium, totam rem aperiam, eaque ipsa quae ab</p>
</div>
<div class="btn" style="left:957px;top:567px;width:131px;height:50px">Sign Up</div>

<!-- About -->
<h2 class="abs section-title" style="left:113px;top:922px">About Us</h2>
<p class="abs about-copy">"Sed ut perspiciatis unde omnis iste natus error sit voluptatem accusantium doloremque laudantium, totam rem aperiam, eaque ipsa quae ab illo inventore veritatis et quasi architecto beatae vitae dicta sunt explicabo. Nemo enim ipsam voluptatem quia voluptas sit aspernatur aut odit aut fugit, sed quia consequuntur magni dolores eos qui ratione voluptatem sequi nesciunt. Neque porro quisquam est, qui dolorem ipsum quia dolor sit amet, consectetur, adipisci velit, sed quia non numquam eius modi tempora incidunt ut labore et dolore magnam aliquam quaerat voluptatem. Ut enim ad minima veniam, quis nostrum exercitationem</p>
<div class="btn" style="left:113px;top:1282px;width:132px;height:49px">Read More</div>
<div class="abs about-accent"></div>
<div class="abs about-photo" role="img" aria-label="Hands holding a tablet showing a streaming movie library"></div>

<!-- Services -->
<div class="abs services"></div>
<h2 class="abs section-title center" style="top:1510px">Our Services</h2>
<p class="abs lead center" style="top:1580px;left:160px;width:880px">"Sed ut perspiciatis unde omnis iste natus error sit voluptatem accusantium doloremque laudantium, totam rem aperiam, eaque ipsa quae ab illo inventore veritatis et quasi architecto beatae vitae dicta sunt</p>

<div class="card" style="left:99px">
  <div class="pic" role="img" aria-label="TV showing a video on demand menu with a remote control" style="background:linear-gradient(160deg,#0c1c3a,#1d4a8a 50%,#0a1020)"></div>
  <h3>Sed ut perspiciatis unde</h3>
  <p>"Sed ut perspiciatis unde omnis iste natus error sit voluptatem accusantium doloremque laudantium, totam rem aperiam, eaque ipsa quae</p>
  <a>Read More</a>
</div>
<div class="card" style="left:443px">
  <div class="pic" role="img" aria-label="Laptop and phone showing streaming titles on a desk" style="background:linear-gradient(160deg,#e8c27a,#d9a956 45%,#4a4f58 70%,#e6d3b0)"></div>
  <h3>Sed ut perspiciatis unde</h3>
  <p>"Sed ut perspiciatis unde omnis iste natus error sit voluptatem accusantium doloremque laudantium, totam rem aperiam, eaque ipsa quae</p>
  <a>Read More</a>
</div>
<div class="card" style="left:786px">
  <div class="pic" role="img" aria-label="Phone held in front of a wall of channel screens" style="background:linear-gradient(160deg,#1a2430,#3c6a8a 50%,#141a22)"></div>
  <h3>Sed ut perspiciatis unde</h3>
  <p>"Sed ut perspiciatis unde omnis iste natus error sit voluptatem accusantium doloremque laudantium, totam rem aperiam, eaque ipsa quae</p>
  <a>Read More</a>
</div>
<div class="btn" style="left:530px;top:2175px;width:140px;height:49px">View More</div>

<!-- Sign up -->
<svg class="abs" style="left:0;top:2315px" width="1200" height="604" viewBox="0 0 1200 604" role="img" aria-label="Red tinted wall of TV screens">
  <defs>
    <linearGradient id="signupFill" x1="0" y1="0" x2="1" y2="1">
      <stop offset="0" stop-color="#ff1a1a"/>
      <stop offset=".5" stop-color="#e00000"/>
      <stop offset="1" stop-color="#c40000"/>
    </linearGradient>
  </defs>
  <path d="M70 2 L1130 32 Q1200 34 1200 100 L1200 520 Q1200 568 1140 570 L70 600 Q0 602 0 540 L0 62 Q0 0 70 2 Z" fill="url(#signupFill)"/>
</svg>
<h2 class="abs section-title center signup-text" style="top:2406px;left:-8px;color:var(--white)">Sign Up Now</h2>
<p class="abs lead center signup-text" style="top:2476px;left:150px;width:885px;color:var(--white)">"Sed ut perspiciatis unde omnis iste natus error sit voluptatem accusantium doloremque laudantium, totam rem aperiam, eaque ipsa quae ab illo inventore veritatis et quasi architecto beatae vitae dicta sunt</p>
<div class="field" style="left:129px">Name</div>
<div class="field" style="left:371px">User Name *</div>
<div class="field" style="left:612px">Membership Tier</div>
<div class="field" style="left:855px;width:201px">Password
  <svg width="22" height="16" viewBox="0 0 22 16"><path d="M1 8 Q11 -3 21 8 Q11 19 1 8 Z" fill="none" stroke="#fff" stroke-width="1.8"/><circle cx="11" cy="8" r="3.2" fill="none" stroke="#fff" stroke-width="1.8"/></svg>
</div>
<div class="btn" style="left:524px;top:2720px;width:139px;height:50px;background:var(--white);color:var(--red)">Sign Up</div>
<div class="abs center" style="top:2802px;left:-8px;font-size:15px;color:var(--white);text-decoration:underline">Forgot Password</div>

<!-- FAQ -->
<div class="abs faq-photo" role="img" aria-label="Person relaxing on a sofa holding a remote toward a TV"></div>
<h2 class="abs section-title" style="left:598px;top:3082px">Latest FAQ’s</h2>
<p class="abs lead" style="left:598px;top:3146px;width:470px;color:var(--muted)">"Sed ut perspiciatis unde omnis iste natus error sit voluptatem accusantium doloremque laudantium,</p>
<div class="faq-item open" style="top:3222px">
  <svg class="sign" viewBox="0 0 18 18"><line x1="2" y1="9" x2="16" y2="9" stroke="#111" stroke-width="2"/></svg>
  Lorem ipsum dolor sit amet, consectetur
</div>
<p class="abs faq-answer">Lorem ipsum dolor sit amet, consectetur adipiscing elit, sed do eiusmod tempor incididunt ut labore et dolore magna aliqua. Quis ipsum suspendisse ultrices gravida. Risus commodo viverra maecenas accumsan lacus vel facilisis.</p>
<div class="faq-item closed" style="top:3375px">
  <svg class="sign" viewBox="0 0 18 18"><line x1="2" y1="9" x2="16" y2="9" stroke="#999" stroke-width="1.6"/><line x1="9" y1="2" x2="9" y2="16" stroke="#999" stroke-width="1.6"/></svg>
  Lorem ipsum dolor sit amet, consectetur
</div>
<div class="faq-item closed" style="top:3445px">
  <svg class="sign" viewBox="0 0 18 18"><line x1="2" y1="9" x2="16" y2="9" stroke="#999" stroke-width="1.6"/><line x1="9" y1="2" x2="9" y2="16" stroke="#999" stroke-width="1.6"/></svg>
  Lorem ipsum dolor sit amet, consectetur
</div>
<div class="btn" style="left:598px;top:3517px;width:140px;height:50px">Read More</div>

<!-- Footer -->
<svg class="abs" style="left:0;top:3725px" width="1200" height="393" viewBox="0 0 1200 393" role="img" aria-label="Dark wall of TV screens">
  <defs>
    <linearGradient id="footerFill" x1="0" y1="0" x2="0" y2="1">
      <stop offset="0" stop-color="#1e1e1e"/>
      <stop offset=".5" stop-color="#0c0c0c"/>
      <stop offset="1" stop-color="#000000"/>
    </linearGradient>
  </defs>
  <path d="M0 100 Q0 42 60 40 L1140 2 Q1200 0 1200 60 L1200 393 L0 393 Z" fill="url(#footerFill)"/>
</svg>
<div class="abs brand light" style="left:502px;top:3850px"><span class="mark"></span>VELTRO</div>
<nav class="footer-nav">
  <a style="left:286px">HOME</a>
  <a style="left:398px">ABOUT US</a>
  <a style="left:543px">OUR PLANS</a>
  <a style="left:700px">FAQ’S</a>
  <a style="left:810px">CONTACT US</a>
</nav>
<span class="social" style="left:545px"></span>
<span class="social" style="left:586px"></span>
<span class="social" style="left:627px"></span>
<div class="abs center copyright" style="left:0">© Copyright 2023 Veltro | All Rights Reserved</div>

</body>
</html>
```